Website Design for Chef Wen Chinese Restaurant

Chef Wen is a new Chinese Restaurant. It offers exceptional dining experience with authentic and dynamic dishes created with quality ingredients.

A vivid website theme is required to promote this new restaurant online. Logo, menu, wine list and a few other files are attached for help with designing.

A very rough demo website has been setup and can be accessed via http://www.chefwen.com.au. It is for telling designers what content is shown up on each page (except for homepage). By reading the about us page, designers can get some more info of Chef Wen. However, the layout, theme color, font, etc are not set in stone. Visitors should be able to feel Chef Wen restaurant's authentic Chinese cuisine and high hygiene standard. Home page of the website could be The "Our website is coming soon" description is shown on demo site but do not required to be presented on new design.

Some main pages design should be included: Home (landing page), About us, Menu (Dishes), Winelist, Gallery, Contact us. No HTML and coding required. The output should be well layered psd or png files with acceptable resolution for web use.

A few other website can be referred to are:

http://larkspurasian.com.au/
http://www.river-lamp.com/
http://tamworthy.com.au/
http://harbelrestaurant.com.au/
http://www.quillerestaurant.com.au/
http://www.thekiln.com.au/

Industry/Entity Type

Restaurant

Requirements
Nice to have
• I expect designs of at least these webpages: homepage, menu page and contact us page. If you can provide "about us" page as well, it will probably help you win the competition. well layered psd or png file is my preference.
Should not have
• You don't have to make html/cs/js or any coding. All I need is just art design

```html
<!DOCTYPE html>
<html lang="en">
<head>
<meta charset="utf-8">
<title>Chef Wen Chinese Restaurant</title>
<link href="https://fonts.googleapis.com/css2?family=Open+Sans:wght@400;600;700&family=Ubuntu:wght@400;500;700&display=swap" rel="stylesheet">
<style>
:root{
  --red:#e30f13;
  --red-dark:#a80a0c;
  --ink:#222222;
  --charcoal:#252525;
  --cream:#fdf6cf;
  --text:#555555;
  --card:#f4f4f4;
  --line:#dddddd;
  --white:#ffffff;
}
*{margin:0;padding:0;box-sizing:border-box}
html,body{width:844px;height:1200px;overflow:hidden;background:var(--white)}
body{position:relative;font-family:"Open Sans",sans-serif;color:var(--text)}
.abs{position:absolute}

.masthead{left:0;top:0;width:844px;height:115px;background:var(--charcoal);border-top:3px solid var(--red)}
.brand{left:360px;top:-24px;width:124px;height:124px;border-radius:50%;background:var(--cream);border:4px solid #7a1b10;box-shadow:0 0 0 3px var(--cream);display:flex;align-items:center;justify-content:center;z-index:3}
.brand span{font-family:"Ubuntu",sans-serif;font-weight:700;font-size:15px;color:var(--red);margin-top:22px}

.nav{left:122px;top:100px;width:601px;height:42px;background:linear-gradient(#ee1519,#c90c0f);z-index:4}
.nav-ear{top:100px;width:16px;height:16px;background:var(--red-dark);z-index:3}
.nav-ear.left{left:108px;clip-path:polygon(100% 0,100% 100%,0 100%)}
.nav-ear.right{left:723px;clip-path:polygon(0 0,100% 100%,0 100%)}
.nav a{position:absolute;top:0;height:42px;line-height:42px;color:var(--white);font-size:10.5px;text-decoration:none;text-transform:uppercase}
.nav a.active{left:24px;top:-1px;height:45px;line-height:45px;width:50px;text-align:center;background:var(--cream);color:var(--red)}

.hero{left:0;top:115px;width:844px;height:397px;background:radial-gradient(ellipse at 60% 45%,#f6dc8c 0%,#e9c46a 25%,#c9875a 50%,#8a3a2c 75%,#5a2a20 100%)}
.hero-title{left:249px;top:264px;width:346px;height:43px;background:var(--red);color:var(--white);font-family:"Ubuntu",sans-serif;font-weight:700;font-size:28px;text-align:center;line-height:43px}
.hero-sub{left:143px;top:317px;width:558px;height:44px;background:var(--ink);color:var(--white);font-family:"Ubuntu",sans-serif;font-weight:400;font-size:18.5px;text-align:center;line-height:44px}
.arrow{top:305px}

.welcome{left:0;top:540px;width:844px;text-align:center;font-size:17px;font-weight:400;color:var(--ink)}
.welcome em{font-style:normal;color:var(--red);margin-left:6px}

.card{top:599px;width:200px;height:223px;background:var(--card);border:1px solid var(--line)}
.card-tag{left:27px;top:-10px;width:146px;height:30px;background:var(--red);color:var(--white);font-family:"Ubuntu",sans-serif;font-weight:700;font-size:11px;text-align:center;line-height:30px;box-shadow:0 3px 3px rgba(0,0,0,.25)}
.card-tag::before,.card-tag::after{content:"";position:absolute;top:0;width:10px;height:10px;background:var(--red-dark)}
.card-tag::before{left:-10px;clip-path:polygon(100% 0,100% 100%,0 100%)}
.card-tag::after{right:-10px;clip-path:polygon(0 0,100% 100%,0 100%)}
.card-photo{left:16px;top:33px;width:166px;height:98px}
.card p{position:absolute;left:10px;top:149px;width:180px;text-align:center;font-size:7.8px;line-height:16px}

.section-title{top:857px;font-size:16.5px;font-weight:400;color:var(--ink)}
.section-title em{font-style:normal;color:var(--red)}
.about-photo{left:99px;top:900px;width:131px;height:102px;background:radial-gradient(circle,#f3e3d3,#c99a62 70%,#a77845)}
.copy{font-size:7.6px;line-height:16px;text-align:justify}
.btn{height:23px;padding:0 11px;background:var(--red);color:var(--white);font-weight:700;font-size:10px;line-height:23px}

.menu-list{left:613px;top:896px;list-style:none;font-size:8.6px;line-height:16.5px}
.menu-list li::before{content:"\2605";color:var(--red);font-size:7px;margin-right:9px}

.footer{left:0;top:1126px;width:844px;height:74px;background:var(--charcoal);border-top:4px solid var(--red);text-align:center;color:var(--white)}
.footer nav{margin-top:18px;font-size:10.5px;letter-spacing:.2px}
.footer small{display:block;margin-top:12px;font-size:8px;color:#ccc}
</style>
</head>
<body>

<header class="abs masthead"></header>
<div class="abs brand"><span>Chef Wen</span></div>

<div class="abs nav-ear left"></div>
<div class="abs nav-ear right"></div>
<nav class="abs nav">
  <a class="active" href="#">Home</a>
  <a style="left:94px" href="#">About Us</a>
  <a style="left:176px" href="#">Menu</a>
  <a style="left:240px" href="#">Wine List</a>
  <a style="left:321px" href="#">Gallery</a>
  <a style="left:396px" href="#">Contact Us</a>
  <a style="left:491px" href="#">Larkspur Court</a>
</nav>

<section class="abs hero" role="img" aria-label="Plate of scrambled eggs with crisp bacon and parsley"></section>
<h1 class="abs hero-title">CHEF WEN VALUES</h1>
<p class="abs hero-sub">CHEF WEN IS NAMED AFTER ITS' EXECUTIVE CHEF, MR WEN.</p>
<svg class="abs arrow" style="left:63px" width="16" height="32" viewBox="0 0 16 32"><path d="M14 2 2 16l12 14" fill="none" stroke="#777" stroke-width="2"/></svg>
<svg class="abs arrow" style="left:769px" width="16" height="32" viewBox="0 0 16 32"><path d="M2 2l12 14L2 30" fill="none" stroke="#777" stroke-width="2"/></svg>

<h2 class="abs welcome">WELCOME TO <em>OUR COMPANY</em></h2>

<article class="abs card" style="left:99px">
  <div class="abs card-tag">LANTERN PREMIUM</div>
  <div class="abs card-photo" role="img" aria-label="Bamboo steamer with green dumplings" style="background:radial-gradient(circle,#cbd3b0,#c49a5c 60%,#8a5a2c)"></div>
  <p>Chef Wen is named after its' executive chef, Larkspur Court, in Kelbrook. Larkspur Court has been running successfully for years due to Chef Wen's talent of cooking.</p>
</article>
<article class="abs card" style="left:322px">
  <div class="abs card-tag">LANTERN PREMIUM</div>
  <div class="abs card-photo" role="img" aria-label="Plate of pan-fried dumplings with herbs" style="background:radial-gradient(circle,#e8d6a8,#eef0f4 65%,#ffffff)"></div>
  <p>Chef Wen is named after its' executive chef, Larkspur Court, in Kelbrook. Larkspur Court has been running successfully for years due to Chef Wen's talent of cooking.</p>
</article>
<article class="abs card" style="left:545px">
  <div class="abs card-tag">LANTERN PREMIUM</div>
  <div class="abs card-photo" role="img" aria-label="Bowl of braised chicken feet in red sauce" style="background:radial-gradient(circle,#e04a2a,#b8321c 55%,#6a3a1c)"></div>
  <p>Chef Wen is named after its' executive chef, Larkspur Court, in Kelbrook. Larkspur Court has been running successfully for years due to Chef Wen's talent of cooking.</p>
</article>

<h2 class="abs section-title" style="left:99px">ABOUT <em>US</em></h2>
<div class="abs about-photo" role="img" aria-label="Bamboo steamer with prawn dumplings"></div>
<p class="abs copy" style="left:250px;top:895px;width:334px">Chef Wen is named after its' executive chef, Mr Wen. Chef Wen had been in his career for nearly two decades before he moved to Australia 9 years ago. He settled in Harrowvale then started his first to Chef Wen's talent of cooking.We offer exceptional dining experience with authentic and dynamic dishes created with quality ingredients.</p>
<p class="abs copy" style="left:250px;top:974px;width:334px">To be able to provide pure Chinese tea, Chef Wen sources genuin high quality tea leaves and courier to Australia by air, thus a wide range of choices are available to our guests.</p>
<p class="abs copy" style="left:99px;top:1019px;width:491px">Taking advantages of Southvale's rich and quality food resources, Chef Wen developed a number of recipes to turn best ingredients into authentic dishes. All dishes are well looked after by Mr Wen's morning or afternoon tea, atday hand made for garenteed freshness</p>
<div class="abs btn" style="left:99px;top:1077px">More</div>

<h2 class="abs section-title" style="left:613px">MENU</h2>
<ul class="abs menu-list">
  <li>Yun Cha</li><li>Entrée</li><li>Soup</li><li>Cold Dishes</li><li>Seafood Dishes</li><li>Pork Dishes</li><li>Tofu Dishes</li><li>Special flavour selections</li><li>Abalone and Sea Cucumber</li><li>Rice and Noodles</li>
</ul>
<div class="abs btn" style="left:614px;top:1077px">More</div>

<footer class="abs footer">
  <nav>Home &nbsp;//&nbsp; About Us &nbsp;//&nbsp; Menu &nbsp;//&nbsp; Wine List &nbsp;//&nbsp; Gallery &nbsp;//&nbsp; Contact Us &nbsp;//&nbsp; Larkspur Court</nav>
  <small>© 2014 - Chef Wen Chinese Restaurant</small>
</footer>

</body>
</html>
```